Refresh Brightpath Coursecraft

Need a new design for e-learning development and web app development site: http://brightpathcoursecraft.example. Need pages for everything on menu bar plus a training services and a web app development services pages and a better page for samples http://brightpathcoursecraft.example/samples5/.

***Must be programmed in html 5. NO CMS. No WP. No Plume. Straight html/css.

Target Market(s)

government

Industry/Entity Type

Government

Coding

Coded - Design and coding required

Number of Pages Required

1 page

Requirements
Must have
• Must be coded in html5/css. No CMS.
• Divided so you can easily see that we offer 3 separate services:
• Live Training - E-Learning Development - Web App Development
• A way to display logos of all our clients like on bottom of this page: https://www.quorvatests.example (this is also our website so you can copy all these logos)
• List both our Denver location which is already on our website plus our office in Velmoro Plaza. Street 62 Sur, 14-87. Santa Orla, Valtierra.
• A page like this for our web app dev services https://www.tekvanu.example/product-development
Should not have
• CMS

```html
<!DOCTYPE html>
<html lang="en">
<head>
<meta charset="utf-8">
<title>Brightpath Coursecraft</title>
<link href="https://fonts.googleapis.com/css2?family=Lato:wght@300;400;700;900&display=swap" rel="stylesheet">
<style>
:root{
  --blue:#1d79c1;
  --blue-deep:#1767a8;
  --orange:#f7a128;
  --ink:#333;
  --muted:#666;
  --grey-bg:#ebebeb;
  --line:#d9d9d9;
}
*{box-sizing:border-box;margin:0;padding:0}
html,body{width:1200px;height:4478px;overflow:hidden}
body{font-family:"Lato",sans-serif;color:var(--ink);background:#fff;position:relative}
.site-header{height:75px;display:flex;align-items:center;justify-content:space-between;padding:0 170px 0 178px}
.brand{display:flex;align-items:center;gap:10px;color:var(--blue);font-weight:700;font-size:17px;letter-spacing:.5px}
.brand-dot{width:34px;height:34px;border-radius:50%;background:var(--orange)}
.main-nav{display:flex;gap:44px;font-size:12px;letter-spacing:.5px;color:#444}
.main-nav a{color:inherit;text-decoration:none}

.hero{position:relative;height:600px;overflow:hidden}
.hero-photo{position:absolute;inset:0;background:linear-gradient(120deg,#6b5a4c 0%,#b5a594 40%,#dcd6cf 60%,#7d7670 100%)}
.hero-circle{position:absolute;left:-130px;top:-70px;width:720px;height:560px;border-radius:50%;background:rgba(29,121,193,.9)}
.hero-title{position:absolute;left:176px;top:118px;width:330px;color:#fff;font-size:33px;font-weight:300;line-height:1.25}
.hero-cta{position:absolute;left:224px;top:356px;width:200px;height:200px;border-radius:50%;background:var(--orange);color:#fff;font-weight:700;font-size:24px;display:flex;align-items:center;justify-content:center;text-align:center;line-height:1.2}
.hero-curve{position:absolute;left:0;bottom:0;width:1200px;height:160px}
.slider-dots{position:absolute;left:516px;top:533px;display:flex;gap:14px}
.slider-dots span{width:42px;height:4px;background:#fff;opacity:.6}
.slider-dots span:first-child{opacity:1}

.section-title{font-size:40px;font-weight:300;text-align:center;color:#222}
.about{height:425px;padding-top:70px}
.about p{width:770px;margin:22px auto 0;font-size:11.5px;line-height:1.9;text-align:center;color:var(--muted)}
.about p+p{margin-top:16px}

.services{background:var(--grey-bg);height:1590px;padding-top:80px}
.intro{width:560px;margin:20px auto 0;font-size:11.5px;line-height:1.8;text-align:center;color:var(--muted)}
.service-card{width:852px;height:362px;margin:50px auto 0;background:#fff;display:flex}
.service-card + .service-card{margin-top:56px}
.service-media{width:426px;height:100%}
.service-body{width:426px;padding:40px 44px 0 24px;position:relative}
.service-card.reverse .service-body{padding:40px 24px 0 40px;text-align:center}
.service-title{font-size:32px;font-weight:300;color:var(--blue);margin:0 0 28px -40px;white-space:nowrap;background:#fff;display:inline-block;padding:6px 24px 6px 30px;border-radius:30px}
.service-card.reverse .service-title{margin:0 -70px 28px 0;padding:6px 30px}
.service-title em{font-style:normal;color:var(--orange)}
.service-body p{font-size:11.5px;line-height:1.95;color:var(--muted);padding-left:36px}
.service-card.reverse .service-body p{padding:0 20px 0 0}
.service-body .btn{margin-left:36px}
.service-card.reverse .btn{margin-left:0}
.btn{display:inline-block;margin-top:24px;padding:9px 22px;border-radius:20px;background:var(--orange);color:#fff;font-size:11px;font-weight:700;letter-spacing:.5px}

.clients{height:740px;padding-top:75px}
.client-grid{width:852px;margin:42px auto 0;display:grid;grid-template-columns:repeat(5,1fr);border-left:1px solid var(--line);border-top:1px solid var(--line)}
.client{height:120px;border-right:1px solid var(--line);border-bottom:1px solid var(--line);display:flex;align-items:center;justify-content:center;gap:8px;font-size:15px;font-weight:700;color:#2a4f86}
.client i{width:18px;height:18px;border-radius:50%;background:#2a4f86;display:block}
.clients .center{text-align:center;margin-top:26px}
.clients .btn{margin-top:0}

.contact{height:622px;background:linear-gradient(#ececec,#fff 140px);padding-top:90px}
.contact h2{font-size:40px;font-weight:300;text-align:center;line-height:1.15;color:#222}
.contact h2 strong{color:var(--blue);font-weight:700}
.contract-table{width:858px;margin:44px auto 0;border-collapse:collapse;font-size:12px}
.contract-table th{height:56px;text-align:left;font-weight:400;color:#fff;padding:0 18px;font-size:13px}
.contract-table td{height:56px;padding:0 18px;border-top:1px solid #fff}
.col-a{background:#dfe6ee;width:212px}
.col-b{background:#fbe9c6;width:384px}
.col-c{background:#e3e3e3}
th.col-a{background:var(--blue)} th.col-b{background:var(--orange)} th.col-c{background:#555}

.locations{display:flex;height:322px}
.locations-info{width:627px;background:var(--blue-deep);color:#fff;padding:55px 0 0 173px}
.locations-info h3{font-size:24px;font-weight:400}
.loc-cols{display:flex;gap:40px;margin-top:28px}
.loc h4{font-size:17px;font-weight:400;margin-bottom:14px}
.loc li{list-style:none;display:flex;gap:8px;font-size:10px;line-height:1.5;margin-bottom:6px;width:210px}
.loc svg{flex:none;margin-top:2px}
.map{flex:1;background:linear-gradient(135deg,#e8e6e1,#d4dde4 60%,#c7d6e3)}

.site-footer{height:104px;display:flex;align-items:center;padding:0 170px 0 178px;justify-content:space-between}
.legal{font-size:10px;color:#555;margin-left:-60px}
.social{display:flex;gap:14px}
.social span{width:18px;height:18px;border-radius:50%;background:#222;display:block}
</style>
</head>
<body>
<header class="site-header">
  <div class="brand"><span class="brand-dot"></span>Brightpath Coursecraft</div>
  <nav class="main-nav"><a>HOME</a><a>SERVICES</a><a>PORTFOLIO</a><a>TEAM &amp; EXPERIENCE</a><a>CONTACTS</a></nav>
</header>

<section class="hero">
  <div class="hero-photo" role="img" aria-label="Photo of a presenter leading a training session at a whiteboard in a meeting room"></div>
  <div class="hero-circle"></div>
  <h1 class="hero-title">We create engaging training that exceed expectations.</h1>
  <div class="hero-cta">Get<br>Started</div>
  <svg class="hero-curve" viewBox="0 0 1200 160" preserveAspectRatio="none"><path d="M0 20 Q600 210 1200 20 L1200 160 L0 160Z" fill="#fff"/><path d="M0 20 Q600 210 1200 20" fill="none" stroke="#1d79c1" stroke-width="4"/></svg>
  <div class="slider-dots"><span></span><span></span><span></span></div>
</section>

<section class="about">
  <h2 class="section-title">About Us</h2>
  <p>Brightpath Coursecraft is a certified small business studio based in Brenwick that plans, writes and builds learning programs for public agencies and private teams. Our catalogue spans self-paced online courses, live webinars, classroom workshops, virtual classrooms, blended programs and interactive simulations, all built to common learning standards. Our learning designers bring decades of combined practice shaping technical and business skill courses across many fields, including healthcare, finance, energy, housing, software, manufacturing, public service, universities and schools, so every audience receives training that fits its work and its learners.</p>
  <p>We offer a bench of 60+ UX and UI designers, Product Owners, Scrum Masters, full-stack developers and more working together to build genuinely useful applications. We can work as an extension of your local team with staff augmentation or entire project development. We adapt our processes to fit our partner's needs and understand the project's objectives, content and users.</p>
</section>

<section class="services">
  <h2 class="section-title">Our Services</h2>
  <p class="intro">Sed ut perspiciatis unde omnis iste natus error sit voluptatem accusantium doloremque laudantium, totam rem aperiam, eaque ipsa quae ab illo inventore veritatis et quasi architecto beatae vitae dicta sunt explicabo nemo enim ipsam voluptatem.</p>

  <article class="service-card">
    <div class="service-media" role="img" aria-label="Photo of a trainer addressing a classroom with raised hands" style="background:linear-gradient(135deg,#c9c3bb,#8a7d72 55%,#3e3a38)"></div>
    <div class="service-body">
      <h3 class="service-title"><em>Live</em> Training</h3>
      <p>Sed ut perspiciatis unde omnis iste natus error sit voluptatem accusantium doloremque laudantium, totam rem aperiam, eaque ipsa quae ab illo inventore veritatis et quasi architecto beatae vitae dicta sunt explicabo. Nemo enim ipsam voluptatem quia voluptas sit aspernatur aut odit aut fugit sed quia consequuntur magni dolores eos qui ratione voluptatem sequi nesciunt.</p>
      <span class="btn">READ MORE</span>
    </div>
  </article>

  <article class="service-card reverse">
    <div class="service-body">
      <h3 class="service-title"><em>E-Learning</em> Development</h3>
      <p>Sed ut perspiciatis unde omnis iste natus error sit voluptatem accusantium doloremque laudantium, totam rem aperiam, eaque ipsa quae ab illo inventore veritatis et quasi architecto beatae vitae dicta sunt explicabo. Nemo enim ipsam voluptatem quia voluptas sit aspernatur aut odit aut fugit sed quia consequuntur magni dolores eos qui ratione voluptatem sequi nesciunt.</p>
      <span class="btn">READ MORE</span>
    </div>
    <div class="service-media" role="img" aria-label="Photo of hands on a laptop with floating digital learning icons" style="background:linear-gradient(135deg,#e7e4df,#b9b1a8 50%,#6d675f)"></div>
  </article>

  <article class="service-card">
    <div class="service-media" role="img" aria-label="Photo of a developer reviewing an app on a phone in front of a monitor" style="background:linear-gradient(135deg,#2c4a78,#6b88b8 50%,#c8d3e3)"></div>
    <div class="service-body">
      <h3 class="service-title"><em>Web App</em> Development</h3>
      <p>Sed ut perspiciatis unde omnis iste natus error sit voluptatem accusantium doloremque laudantium, totam rem aperiam, eaque ipsa quae ab illo inventore veritatis et quasi architecto beatae vitae dicta sunt explicabo. Nemo enim ipsam voluptatem quia voluptas sit aspernatur aut odit aut fugit sed quia consequuntur magni dolores eos qui ratione voluptatem sequi nesciunt.</p>
      <span class="btn">READ MORE</span>
    </div>
  </article>
</section>

<section class="clients">
  <h2 class="section-title">Our Clients</h2>
  <p class="intro">Sed ut perspiciatis unde omnis iste natus error sit voluptatem accusantium doloremque laudantium, totam rem aperiam, eaque ipsa quae ab illo inventore veritatis et quasi architecto beatae vitae dicta sunt.</p>
  <div class="client-grid">
    <div class="client"><i></i>Skyward Corps</div>
    <div class="client"><i></i>Halden Univ.</div>
    <div class="client"><i></i>Oakvale Dept.</div>
    <div class="client"><i></i>Ridgeline</div>
    <div class="client">Clarevo</div>
    <div class="client"><i></i>Nuvessa</div>
    <div class="client"><i></i>Corvin Inst.</div>
    <div class="client">Ashmere</div>
    <div class="client">Pinecrest University</div>
    <div class="client"><i></i>Fibrova</div>
    <div class="client"><i></i>Marlow County</div>
    <div class="client">Redfield State</div>
    <div class="client"><i></i>Tallis Agency</div>
    <div class="client"><i></i>Westbrook</div>
    <div class="client"><i></i>Kestrel Co.</div>
  </div>
  <div class="center"><span class="btn">VIEW ALL CLIENTS</span></div>
</section>

<section class="contact">
  <h2>Contact Us Today for a Free<br>Consultation <strong>555-014-7720 x310</strong></h2>
  <table class="contract-table">
    <tr><th class="col-a">Most Common<br>Labor Categories</th><th class="col-b">Contract Information</th><th class="col-c">Contract Vehicles</th></tr>
    <tr><td class="col-a">Instructional Designer</td><td class="col-b">CAGE code 7KRM2</td><td class="col-c">SBA 8(a) Case Number: 41852R</td></tr>
    <tr><td class="col-a">E-Learning Project Manager</td><td class="col-b">GSA PSS Schedule 874 GS-00F-118KX</td><td class="col-c">Certified HUBzone</td></tr>
    <tr><td class="col-a">Graphic Designer</td><td class="col-b">Primary NAICS 600920 Professional Development Training</td><td class="col-c">GSA PSS Schedule 874 GS-00F-118KX</td></tr>
    <tr><td class="col-a">Webinar Producer</td><td class="col-b">500301 500302 500310 600920 600940 600955 500418</td><td class="col-c">Native American owned</td></tr>
  </table>
</section>

<section class="locations">
  <div class="locations-info">
    <h3>Contacts</h3>
    <div class="loc-cols">
      <div class="loc">
        <h4>Location 1</h4>
        <ul>
          <li><svg width="9" height="12" viewBox="0 0 9 12"><path d="M4.5 0a4.5 4.5 0 0 0-4.5 4.5C0 8 4.5 12 4.5 12S9 8 9 4.5A4.5 4.5 0 0 0 4.5 0z" fill="#fff"/></svg>4820 Larkfield Avenue, Suite B-210<br>Brenwick, CO 80990</li>
          <li><svg width="10" height="10" viewBox="0 0 10 10"><path d="M2 0l2 2.5-1.2 1.3a6 6 0 0 0 3.4 3.4L7.5 6 10 8l-1.5 2C4 10 0 6 0 1.5z" fill="#fff"/></svg>Telephone: +1-555-014-7720</li>
          <li><svg width="11" height="8" viewBox="0 0 11 8"><rect width="11" height="8" fill="#fff"/><path d="M0 0l5.5 4.5L11 0" stroke="#1767a8" fill="none"/></svg>E-mail: hello@brightpath.example</li>
        </ul>
      </div>
      <div class="loc">
        <h4>Location 2</h4>
        <ul>
          <li><svg width="9" height="12" viewBox="0 0 9 12"><path d="M4.5 0a4.5 4.5 0 0 0-4.5 4.5C0 8 4.5 12 4.5 12S9 8 9 4.5A4.5 4.5 0 0 0 4.5 0z" fill="#fff"/></svg>Velmoro Plaza. Street 62 Sur,<br>14-87. Santa Orla, Valtierra.</li>
        </ul>
      </div>
    </div>
  </div>
  <div class="map" role="img" aria-label="Street map showing the office location"></div>
</section>

<footer class="site-footer">
  <div class="brand"><span class="brand-dot"></span>Brightpath Coursecraft</div>
  <p class="legal">© 2019 All Rights Reserved. Privacy Policy | Terms of Use | Contact</p>
  <div class="social" aria-label="Social links"><span></span><span></span><span></span></div>
</footer>
</body>
</html>
```